Need Flyer for Our Real estate Agency

Need to run General Campaign for our agency with Start of New Year as our theme ..Must have an agent's picture on the DL..
Address:
27 / 486Brindle rd, Marsden VIC 3047
Ph:03 9412 7306
email:info@kovalinrealestate.com.au
www.kovalinrealestate.com.au
Something like as attached picture..
Target Market(s)
Home Buyers
Industry/Entity Type
Real Estate Agent
Requirements
Must have
- Our Logo Colours

```html
<!DOCTYPE html>
<html lang="en">
<head>
<meta charset="utf-8">
<title>Kovalin Real Estate – New Year DL Flyer</title>
<link rel="stylesheet" href="https://fonts.googleapis.com/css2?family=Cinzel:wght@500&family=Lato:wght@300;400;700;900&display=swap">
<style>
  :root {
    --navy: #0f2a6b;
    --navy-deep: #0a1e50;
    --navy-light: #1a3a86;
    --maroon: #7a1420;
    --maroon-deep: #621019;
    --swoosh-grey: #c9ccd3;
    --white: #ffffff;
    --page: #e9e7e4;
  }
  * { margin: 0; padding: 0; box-sizing: border-box; }
  html, body { width: 1200px; height: 1199px; overflow: hidden; }
  body {
    background: var(--page);
    font-family: "Lato", Arial, sans-serif;
    color: var(--white);
    position: relative;
  }
  .flyer {
    position: absolute;
    left: 117px;
    width: 966px;
    height: 461px;
    box-shadow: 0 6px 16px rgba(0,0,0,.25);
    overflow: hidden;
  }
  .flyer--front { top: 112px; }
  .flyer--back { top: 640px; }
  .flyer__bg { position: absolute; inset: 0; width: 100%; height: 100%; }

  .brand {
    position: absolute;
    left: 502px;
    width: 400px;
    text-align: center;
    display: flex;
    justify-content: center;
    align-items: center;
    gap: 12px;
    font-family: "Cinzel", Georgia, serif;
    font-weight: 500;
    font-size: 36px;
    letter-spacing: 3px;
    color: var(--white);
  }
  .brand__mark { width: 14px; height: 14px; background: var(--white); }

  .flyer--front .brand { top: 70px; }
  .headline {
    position: absolute;
    left: 502px; width: 400px;
    top: 218px;
    text-align: center;
    font-weight: 300;
    font-size: 31px;
    line-height: 1.4;
  }
  .tagline {
    position: absolute;
    left: 452px; width: 500px;
    top: 325px;
    text-align: center;
    font-size: 15.5px;
    letter-spacing: .2px;
  }
  .tagline strong { font-weight: 900; }
  .call-pill {
    position: absolute;
    left: 520px; width: 363px; height: 46px;
    top: 370px;
    background: var(--white);
    border-radius: 23px;
    box-shadow: 0 3px 6px rgba(0,0,0,.35);
    display: flex; align-items: center; justify-content: center; gap: 9px;
    color: var(--maroon);
    font-weight: 900;
    font-size: 20px;
  }
  .call-pill svg { width: 20px; height: 20px; }
  .appraisal-note {
    position: absolute;
    left: 502px; width: 400px;
    top: 428px;
    text-align: center;
    font-size: 17px;
    font-weight: 400;
  }

  .flyer--back .brand { top: 120px; }
  .contact-list {
    position: absolute;
    left: 575px; top: 232px;
    list-style: none;
  }
  .contact-list li {
    display: flex; align-items: center; gap: 16px;
    font-size: 18px;
    height: 40px;
  }
  .contact-list svg { width: 19px; height: 19px; }
  .office-address {
    position: absolute;
    left: 450px; width: 516px;
    top: 420px;
    text-align: center;
    font-size: 18px;
    letter-spacing: .3px;
  }
</style>
</head>
<body>

<section class="flyer flyer--front">
  <svg class="flyer__bg" viewBox="0 0 966 461" preserveAspectRatio="none">
    <defs>
      <linearGradient id="navyFront" x1="0" y1="0" x2="1" y2="1">
        <stop offset="0" stop-color="#1a3a86"/>
        <stop offset=".6" stop-color="#0f2a6b"/>
        <stop offset="1" stop-color="#0a1e50"/>
      </linearGradient>
      <linearGradient id="agentPhoto" x1="0" y1="0" x2="0" y2="1">
        <stop offset="0" stop-color="#b9c8db"/>
        <stop offset=".45" stop-color="#8d8f98"/>
        <stop offset=".7" stop-color="#2f5fb4"/>
        <stop offset="1" stop-color="#4d7a35"/>
      </linearGradient>
    </defs>
    <rect width="966" height="461" fill="url(#navyFront)"/>
    <rect y="388" width="966" height="5" fill="var(--white)"/>
    <rect y="393" width="966" height="68" fill="var(--maroon)"/>
    <path d="M0 0 H365 Q478 200 408 461 H0 Z" fill="var(--swoosh-grey)"/>
    <path d="M0 0 H330 Q452 200 388 461 H0 Z" fill="var(--white)"/>
    <path d="M0 0 H295 Q420 205 376 461 H0 Z" fill="url(#agentPhoto)" role="img" aria-label="Photo of the agent in a blue blazer standing in front of a large two-storey family home"/>
  </svg>

  <div class="brand"><span class="brand__mark"></span>Kovalin Real Estate</div>
  <p class="headline">Curios to know what your<br>home is worth?</p>
  <p class="tagline">START OF NEW YEAR WITH <strong>MIRA DALTON</strong> AND FIND OUT!</p>
  <div class="call-pill">
    <span>CALL ME NOW!</span>
    <svg viewBox="0 0 24 24"><circle cx="12" cy="12" r="10.5" fill="none" stroke="currentColor" stroke-width="2"/><path d="M8.5 7.5 l2 0 1 2.5-1.3 1 a7 7 0 0 0 2.8 2.8 l1-1.3 2.5 1 0 2 c-4.5 .5-8.5-3.5-8-8z" fill="currentColor"/></svg>
    <span>03 9412 7306</span>
  </div>
  <p class="appraisal-note">For Free property Appraisal</p>
</section>

<section class="flyer flyer--back">
  <svg class="flyer__bg" viewBox="0 0 966 461" preserveAspectRatio="none">
    <defs>
      <linearGradient id="navyBack" x1="0" y1="0" x2="1" y2="1">
        <stop offset="0" stop-color="#1a3a86"/>
        <stop offset=".6" stop-color="#0f2a6b"/>
        <stop offset="1" stop-color="#0a1e50"/>
      </linearGradient>
      <radialGradient id="handsPhoto" cx=".45" cy=".5" r=".7">
        <stop offset="0" stop-color="#d9645c"/>
        <stop offset=".35" stop-color="#c99a86"/>
        <stop offset=".7" stop-color="#3a4a66"/>
        <stop offset="1" stop-color="#1c2a44"/>
      </radialGradient>
    </defs>
    <rect width="966" height="461" fill="url(#navyBack)"/>
    <rect y="388" width="966" height="5" fill="var(--white)"/>
    <rect y="393" width="966" height="68" fill="var(--maroon)"/>
    <path d="M0 0 H365 Q478 200 408 461 H0 Z" fill="var(--swoosh-grey)"/>
    <path d="M0 0 H330 Q452 200 388 461 H0 Z" fill="var(--white)"/>
    <path d="M0 0 H295 Q420 205 376 461 H0 Z" fill="url(#handsPhoto)" role="img" aria-label="Photo of two hands sheltering a small red model house"/>
  </svg>

  <div class="brand"><span class="brand__mark"></span>Kovalin Real Estate</div>
  <ul class="contact-list">
    <li>
      <svg viewBox="0 0 24 24"><circle cx="12" cy="12" r="10.5" fill="none" stroke="#fff" stroke-width="1.8"/><path d="M8.5 7.5 l2 0 1 2.5-1.3 1 a7 7 0 0 0 2.8 2.8 l1-1.3 2.5 1 0 2 c-4.5 .5-8.5-3.5-8-8z" fill="#fff"/></svg>
      03 9412 7306
    </li>
    <li>
      <svg viewBox="0 0 24 24"><circle cx="12" cy="12" r="10.5" fill="none" stroke="#fff" stroke-width="1.8"/><rect x="7" y="8.5" width="10" height="7" fill="none" stroke="#fff" stroke-width="1.5"/><path d="M7 8.5 l5 4 5-4" fill="none" stroke="#fff" stroke-width="1.5"/></svg>
      info@kovalinrealestate.com.au
    </li>
    <li>
      <svg viewBox="0 0 24 24"><circle cx="12" cy="12" r="10.5" fill="none" stroke="#fff" stroke-width="1.8"/><circle cx="12" cy="12" r="5.5" fill="none" stroke="#fff" stroke-width="1.3"/><path d="M6.5 12 h11 M12 6.5 c-3 3-3 8 0 11 M12 6.5 c3 3 3 8 0 11" fill="none" stroke="#fff" stroke-width="1.2"/></svg>
      www.kovalinrealestate.com.au
    </li>
  </ul>
  <p class="office-address">27 / 486 Brindle Rd, Marsden VIC 3047</p>
</section>

</body>
</html>
```